New Business Card for Software Company

We are looking at rebranding a 10 year old company that specializes in PDF and DWF solutions for Architects and Engineers. We will attach the new company logo that we are going with so you can work with that and complimentary colors.
The sample information we would like on the business card is:
Gerald Pinfold
Vice President
4738 W. Harrowgate Lane. STE 305
PMB#417
Mesa, AZ 85374
866-392-5074 US Toll Free
123-456-3190 Cell
gpinfold@plavorix.com
The old tag line that we had on the business cars was.
Delivering Dependable Drawing and Document Tools to Design Teams Everywhere.
If you have an idea for a better tag line we are open to that also.
Updates
We would like to thank all of the Designers for their wonderful work. We apologize that we will not have the time to provide feedback to everyone. There is just so many innovative and professional designs that you have all created making our decision even harder.
Target Market(s)
Architects and Engineers
Industry/Entity Type
Business
Look and feel

```html
<!DOCTYPE html>
<html lang="en">
<head>
<meta charset="utf-8">
<title>Plavorix Business Card</title>
<link rel="stylesheet" href="https://fonts.googleapis.com/css2?family=Arimo:wght@400;700&family=Open+Sans:wght@400&display=swap">
<style>
  :root {
    --bg: #e6e6ec;
    --card: #ffffff;
    --orange: #e85a1e;
    --orange-light: #f39a2b;
    --red: #d8342a;
    --grey-text: #555555;
    --card-shadow: rgba(40, 40, 60, 0.18);
  }
  * { margin: 0; padding: 0; box-sizing: border-box; }
  html, body {
    width: 1200px; height: 987px; overflow: hidden;
    background: var(--bg);
  }
  .stage { position: relative; width: 1200px; height: 987px; }
  .card {
    position: absolute; left: 250px; width: 700px; height: 400px;
    background: var(--card); border-radius: 28px;
    box-shadow: 0 8px 24px var(--card-shadow);
    overflow: hidden;
  }
  .card--back { top: 60px; }
  .card--front { top: 527px; font-family: "Arimo", Arial, sans-serif; }

  /* Back */
  .brand-large {
    position: absolute; left: 120px; top: 110px;
    font-family: "Arimo", Arial, sans-serif; font-weight: 700;
    font-size: 110px; letter-spacing: -5px; line-height: 1;
    color: var(--orange);
  }
  .tagline {
    position: absolute; left: 90px; top: 250px; width: 540px;
    font-family: "Open Sans", Arial, sans-serif; font-size: 21px;
    line-height: 1.25; color: var(--grey-text); text-align: center;
  }

  /* Front */
  .accent-bar {
    position: absolute; left: 0; top: 26px; width: 10px; height: 56px;
    background: linear-gradient(var(--red), var(--orange-light));
  }
  .person-name {
    position: absolute; left: 40px; top: 30px;
    font-weight: 700; font-size: 27px; color: var(--orange);
  }
  .person-title {
    position: absolute; left: 40px; top: 62px;
    font-size: 18px; color: var(--grey-text);
  }
  .address {
    position: absolute; left: 40px; top: 112px;
    font-size: 18px; line-height: 1.3; color: var(--grey-text);
    font-style: normal;
  }
  .contacts {
    position: absolute; left: 40px; top: 215px; list-style: none;
    font-size: 18px; line-height: 1.55; color: var(--grey-text);
  }
  .contacts li { display: flex; align-items: center; gap: 8px; }
  .contacts svg { width: 14px; height: 14px; fill: var(--orange); }
  .contacts .email { margin-top: 6px; }
  .brand-small {
    position: absolute; left: 330px; top: 265px;
    display: flex; align-items: center; gap: 12px;
  }
  .brand-small .dot {
    width: 56px; height: 56px; border-radius: 50%; background: var(--orange);
  }
  .brand-small .name {
    font-weight: 700; font-size: 66px; letter-spacing: -3px; line-height: 1;
    color: var(--orange);
  }
</style>
</head>
<body>
<main class="stage">
  <section class="card card--back" aria-label="Card back">
    <div class="brand-large">Plavorix</div>
    <p class="tagline">Delivering Dependable Drawing and Document Tools<br>to Design Teams Everywhere</p>
  </section>

  <section class="card card--front" aria-label="Card front">
    <div class="accent-bar"></div>
    <h1 class="person-name">Gerald Pinfold</h1>
    <p class="person-title">Vice President</p>
    <address class="address">
      4738 W. Harrowgate Lane<br>
      STE 305<br>
      PMB#417, Mesa, AZ 85374
    </address>
    <ul class="contacts">
      <li>
        <svg viewBox="0 0 16 16" aria-hidden="true"><path d="M3 1l3 3-1.5 2a9 9 0 0 0 5.5 5.5L12 10l3 3-2 2C7 15 1 9 1 3z"/></svg>
        866-392-5074(US) TF
      </li>
      <li>
        <svg viewBox="0 0 16 16" aria-hidden="true"><path d="M4 0h8v16H4zM5.5 2v10h5V2zM7 13.5h2v1H7z"/></svg>
        123-456-3190
      </li>
      <li class="email">gpinfold@plavorix.com</li>
    </ul>
    <div class="brand-small">
      <span class="dot"></span>
      <span class="name">Plavorix</span>
    </div>
  </section>
</main>
</body>
</html>
```